Interior Design & Furniture E commerce Website Design

I need a cutting edge website design, this is for Interior Design Services as well as eCommerce for furniture and home decor www.lorivexstudio.com
Here is a sample of the concept behind the site.
I am a furniture & Interior Designer, want to create a life style brand.
Will offer Interior Design Services : Commercial & Residential (this portion will be a catalog or portfolio type)
The eCommerce side will sell, Furniture, Lighting, Decor, Gifts, Textiles, will also be offering trade so that could be at bottom of site. I also like the concept of concierge as where all the info falls under: shipping, etc..

*Please make sure to make the eCommerce prominent.

Gathering more feedback

Hello Designers, I also would like to possibly update my logo, the current one I like but don't Love.

Target Market(s)

High end customers with disposable income, who also appreciate quality and unique furniture & design

Number of Pages Required

5+ page

Colors
0255a3
f37122

Requirements
Must have
• Room Planer: I will be using this tool http://qtstudio.velbarnix.com/room-planner.inc
• Live Chat
• Will be offering 3d renderings for spaces as well as Virtual Reality
• The image I loaded that looks like copper, I would like to have that as a color on the site with the texture: so the colors are Blue and copper. Would like the site to be user friendly and interactive
• http://qtstudio.velbarnix.com/ (this is the current site in development, so we will be offering Design your own, Trends, inspiration, etc...
• I have included a headshot to use for now about me. or about us.
• I also included several actual project installation (residential and commercial) as well as a variety of my furniture items
• I have Included an old Bio and some articles I would like to show case in a Press Area
• I would also like to include a section for Events (Giving back )I do a lot of charity events 1-2 a year and would like to showcase that as well
• *Please make the store (ecommerce prominent )

```html
<!DOCTYPE html>
<html lang="en">
<head>
<meta charset="utf-8">
<title>Lori Vex Studio — Interior Design Services</title>
<link href="https://fonts.googleapis.com/css2?family=Lato:wght@400;700;900&family=Montserrat:wght@400;500;600&display=swap" rel="stylesheet">
<style>
:root{
  --blue:#0255a3;
  --orange:#f37122;
  --ink:#333;
  --muted:#777;
  --light:#f2f2f2;
  --dark:#1c1c1c;
  --white:#fff;
  --gold:#c9a24a;
  --stars:#e2b23a;
}
*{box-sizing:border-box;margin:0;padding:0}
html,body{width:1200px;height:5341px;overflow:hidden}
body{position:relative;font-family:"Lato",sans-serif;color:var(--ink);background:var(--white)}
.abs{position:absolute}
.ph{position:absolute;display:block}
.btn{position:absolute;display:flex;align-items:center;justify-content:center;font:700 15px "Lato",sans-serif;letter-spacing:.5px;text-transform:uppercase}
.btn-orange{background:var(--orange);color:var(--white)}
.btn-blue{background:var(--blue);color:var(--white)}
.btn-white{background:var(--white);color:var(--orange)}
.lorem{font-size:14px;line-height:1.55;color:#555}

/* hero */
.hero{position:absolute;left:0;top:0;width:1200px;height:676px;background:#3a3530}
.nav{position:absolute;left:78px;top:34px;display:flex;gap:34px;font:600 13px "Montserrat",sans-serif;color:var(--white);letter-spacing:.5px}
.nav-rule{position:absolute;left:78px;top:72px;width:1044px;height:1px;background:rgba(255,255,255,.45)}
.nav-tools{position:absolute;right:78px;top:26px;display:flex;align-items:center;gap:26px;color:var(--white);font:600 13px "Montserrat",sans-serif}
.cart{width:34px;height:34px;border-radius:50%;background:var(--orange)}
.brand-mark{position:absolute;left:480px;top:150px;width:240px;height:130px;display:flex;flex-direction:column;align-items:center;justify-content:center;gap:12px}
.brand-mark .sq{width:62px;height:62px;border:2px solid var(--white)}
.brand-mark span{font:700 15px "Lato",sans-serif;color:var(--white);letter-spacing:2px;white-space:nowrap}
.hero-title{position:absolute;left:0;top:368px;width:1200px;text-align:center;font:900 50px "Lato",sans-serif;color:var(--white);letter-spacing:1px}
.hero-sub{position:absolute;left:0;top:436px;width:1200px;text-align:center;font:700 22px "Lato",sans-serif;color:var(--white)}
.arrow{position:absolute;width:56px;height:56px;border-radius:50%;display:flex;align-items:center;justify-content:center}

/* welcome */
.welcome{position:absolute;left:78px;top:612px;width:502px;height:528px;background:var(--orange);color:var(--white)}
.welcome h3{position:absolute;left:40px;top:40px;font:400 26px "Lato",sans-serif}
.welcome h2{position:absolute;left:40px;top:78px;font:700 34px "Lato",sans-serif}
.welcome .avatar{left:40px;top:150px;width:110px;height:110px;border-radius:50%;background:radial-gradient(circle,#d9b89a,#7d5a44);border:3px solid #fff}
.welcome p{position:absolute;left:170px;top:148px;width:300px;font-size:13px;line-height:1.6}
.welcome .btn{left:40px;top:398px;width:168px;height:56px}

/* 3d */
.excursion{position:absolute;left:0;top:1210px;width:1200px;height:590px;background:var(--light)}
.section-title{position:absolute;left:0;width:1200px;text-align:center;font:400 38px "Montserrat",sans-serif}
.thumb-row{position:absolute;left:730px;width:400px;height:130px}
.thumb-row .ph{left:0;top:0;width:160px;height:130px}
.thumb-row h4{position:absolute;left:188px;top:12px;width:210px;font:400 17px "Montserrat",sans-serif;color:var(--orange);line-height:1.35}
.thumb-row small{position:absolute;left:188px;top:84px;font-size:14px;color:#555}

/* services */
.service-title{position:absolute;font:400 38px "Montserrat",sans-serif;color:var(--orange)}
.service-text{position:absolute;width:470px}

/* products */
.products{position:absolute;left:0;top:2830px;width:1200px;height:552px;background:#f5f5f5}
.products h2{position:absolute;left:78px;top:20px;font:400 38px "Montserrat",sans-serif;color:var(--orange)}
.card{position:absolute;top:100px;width:250px;text-align:center}
.card .ph{position:relative;width:250px;height:262px;background-color:#fff;border:1px solid #ddd;box-shadow:0 2px 6px rgba(0,0,0,.08)}
.card h5{margin-top:22px;font:700 17px "Lato",sans-serif;color:var(--orange)}
.stars{margin-top:8px;color:var(--stars);font-size:13px;letter-spacing:1px}
.old{margin-top:6px;font-size:15px;color:#999;text-decoration:line-through}
.price{margin-top:6px;font-size:16px;color:#333}
.card-actions{position:absolute;left:0;top:232px;width:250px;height:30px;display:flex}
.card-actions span{flex:1;background:var(--blue);border-right:1px solid #fff;display:flex;align-items:center;justify-content:center}

/* catalog */
.rule-title{position:absolute;left:0;width:1200px;display:flex;align-items:center;justify-content:center;gap:28px;font:400 38px "Montserrat",sans-serif}
.rule-title i{display:block;width:220px;height:1px;background:currentColor;opacity:.6}
.tile{position:absolute;width:290px;height:205px}

/* newsletter */
.newsletter{position:absolute;left:0;top:4094px;width:1200px;height:427px}
.newsletter h2{position:absolute;left:0;top:92px;width:1200px;text-align:center;font:400 34px "Montserrat",sans-serif;color:var(--blue)}
.newsletter p{position:absolute;left:400px;top:150px;width:400px;text-align:center;font-size:14px;color:#555;line-height:1.5}
.field{position:absolute;left:310px;top:268px;width:428px;height:62px;background:#fff;border:1px solid #ccc;font-size:14px;color:#888;padding-left:20px;display:flex;align-items:center}

/* articles */
.articles{position:absolute;left:0;top:4521px;width:1200px;height:481px;background:var(--orange)}
.mag{position:absolute;top:150px;width:238px;height:278px;background:#fff}

/* footer */
.footer{position:absolute;left:0;top:5002px;width:1200px;height:267px;background:var(--dark);color:#ccc}
.footer h4{position:absolute;font:700 17px "Lato",sans-serif;color:#fff;letter-spacing:1px}
.footer .lines{position:absolute;font-size:14px;line-height:1.7}
.footer .hl{color:var(--orange)}
.foot-nav{position:absolute;left:0;top:200px;width:1200px;text-align:center;font-size:14px;color:#ccc;word-spacing:6px}
.copy{position:absolute;left:0;top:5269px;width:1200px;height:72px;background:var(--orange);color:#fff;display:flex;align-items:center;justify-content:center;font-size:14px}
</style>
</head>
<body>

<header class="hero">
  <div class="ph" role="img" aria-label="Photograph of a luxury living room with ceiling fan and arched windows" style="inset:0;background:radial-gradient(ellipse 70% 45% at 50% 60%,rgba(222,196,150,.55),transparent 70%),linear-gradient(180deg,#2b2520 0%,#6b5a46 45%,#4a4540 75%,#2e2d2f 100%)"></div>
  <nav class="nav"><span>HOME</span><span>ABOUT</span><span>SERVICES</span><span>SHOP</span><span>PORTFOLIO</span><span>CONTACT</span><span>BLOG</span></nav>
  <div class="nav-tools">
    <svg width="22" height="22" viewBox="0 0 22 22"><circle cx="9" cy="9" r="7" fill="none" stroke="#fff" stroke-width="2.5"/><line x1="14" y1="14" x2="20" y2="20" stroke="#fff" stroke-width="3"/></svg>
    <span class="cart"></span>
    <span>LOGIN</span>
  </div>
  <div class="nav-rule"></div>
  <div class="brand-mark"><div class="sq"></div><span>LORI VEX STUDIO</span></div>
  <h1 class="hero-title">LORI VEX STUDIO</h1>
  <p class="hero-sub">Interior Design Services</p>
  <div class="arrow" style="left:44px;top:375px;background:var(--orange)"><svg width="16" height="24"><polyline points="12,2 3,12 12,22" fill="none" stroke="#fff" stroke-width="3"/></svg></div>
  <div class="arrow" style="left:1100px;top:375px;background:#fff"><svg width="16" height="24"><polyline points="4,2 13,12 4,22" fill="none" stroke="#333" stroke-width="3"/></svg></div>
</header>

<section class="welcome">
  <h3>Welcome to</h3>
  <h2>LORI VEX STUDIO</h2>
  <div class="ph avatar" role="img" aria-label="Portrait headshot of the designer"></div>
  <p>As a child, Lori Vex spent many happy hours in the workshop beside her father, learning how fine furniture is made by hand. She later joined the family business and grew it into a studio for bespoke design. Today she brings this passion for detail, crafted pieces and warm, personal spaces to every home and commercial project she takes on.</p>
  <span class="btn btn-white">Read More</span>
</section>
<div class="ph" role="img" aria-label="Photo of a green dining room interior" style="left:598px;top:694px;width:250px;height:178px;background:radial-gradient(ellipse at 50% 70%,#a89a6a,transparent 60%),linear-gradient(135deg,#2f3a1f,#6d7a3e)"></div>
<div class="ph" role="img" aria-label="Photo of a red lounge interior" style="left:865px;top:694px;width:257px;height:178px;background:radial-gradient(ellipse at 50% 65%,#d77a55,transparent 60%),linear-gradient(135deg,#3e1510,#8c2f22)"></div>
<div class="ph" role="img" aria-label="Photo of a living room with fireplace and white armchairs" style="left:598px;top:890px;width:524px;height:250px;background:radial-gradient(ellipse 30% 40% at 50% 55%,#e89a52,transparent 70%),radial-gradient(ellipse 18% 35% at 20% 75%,#f4efe8,transparent 70%),radial-gradient(ellipse 18% 35% at 80% 75%,#f4efe8,transparent 70%),linear-gradient(135deg,#5a2e1e,#a9765a 60%,#d9c8b4)"></div>

<section class="excursion">
  <h2 class="section-title" style="top:60px;color:var(--blue)">Would you like to try 3D excursion</h2>
  <div class="ph" role="img" aria-label="Video preview of a living room with yellow armchair" style="left:78px;top:143px;width:624px;height:417px;background:radial-gradient(ellipse 20% 22% at 75% 72%,#e5c23c,transparent 70%),radial-gradient(ellipse 30% 18% at 25% 72%,#8a8f94,transparent 70%),linear-gradient(90deg,#8f8478,#d2c9ba 55%,#5f5a52)"></div>
  <svg class="abs" style="left:350px;top:314px" width="80" height="80" viewBox="0 0 80 80"><circle cx="40" cy="40" r="36" fill="none" stroke="#fff" stroke-width="4"/><circle cx="40" cy="40" r="30" fill="#f37122"/><polygon points="32,26 56,40 32,54" fill="#fff"/></svg>
  <div class="thumb-row" style="top:143px">
    <div class="ph" style="background:var(--blue)"></div>
    <svg class="abs" style="left:66px;top:52px" width="26" height="26"><circle cx="11" cy="11" r="8" fill="none" stroke="#fff" stroke-width="2.5"/><line x1="17" y1="17" x2="24" y2="24" stroke="#fff" stroke-width="3"/></svg>
    <h4>Lorem Ipsum is simply and typesetting industry</h4><small>Lorem Ipsum simply dummy</small>
  </div>
  <div class="thumb-row" style="top:287px">
    <div class="ph" role="img" aria-label="Thumbnail of a room interior with yellow chair" style="background:radial-gradient(ellipse at 65% 70%,#d9b640,transparent 50%),linear-gradient(135deg,#6b6258,#cdbfa8)"></div>
    <h4>Lorem Ipsum is simply and typesetting industry</h4><small>Lorem Ipsum simply dummy</small>
  </div>
  <div class="thumb-row" style="top:431px">
    <div class="ph" role="img" aria-label="Thumbnail of a room interior with yellow chair" style="background:radial-gradient(ellipse at 40% 70%,#d9b640,transparent 50%),linear-gradient(135deg,#5e584e,#c9bfae)"></div>
    <h4>Lorem Ipsum is simply and typesetting industry</h4><small>Lorem Ipsum simply dummy</small>
  </div>
</section>

<section>
  <div class="ph" role="img" aria-label="Photo of a commercial lounge with yellow curved seating" style="left:0;top:1851px;width:598px;height:470px;background:radial-gradient(ellipse 45% 30% at 55% 78%,#d6a12c,transparent 70%),radial-gradient(ellipse 35% 20% at 40% 45%,#f2f0ea,transparent 70%),linear-gradient(135deg,#9fb0bd,#d9dee2 45%,#b9a27a)"></div>
  <h2 class="service-title" style="left:658px;top:1900px">Commercial Services</h2>
  <p class="service-text lorem" style="left:658px;top:1960px">Lorem Ipsum is simply dummy text of the printing and typesetting industry. Lorem Ipsum has been the industry's standard dummy text ever since the 1500s, when an unknown printer took a galley of type and scrambled it to make a type specimen book. It has survived not only five centuries, but also the leap into electronic typesetting, remaining essentially unchanged. It was popularised in the 1960s with the release of Letraset sheets containing Lorem Ipsum passages, and more recently with desktop publishing software.</p>
  <span class="btn btn-blue" style="left:658px;top:2198px;width:168px;height:60px">Read More</span>

  <h2 class="service-title" style="left:78px;top:2372px">Recidental Services</h2>
  <p class="service-text lorem" style="left:78px;top:2432px">Lorem Ipsum is simply dummy text of the printing and typesetting industry. Lorem Ipsum has been the industry's standard dummy text ever since the 1500s, when an unknown printer took a galley of type and scrambled it to make a type specimen book. It has survived not only five centuries, but also the leap into electronic typesetting, remaining essentially unchanged. It was popularised in the 1960s with the release of Letraset sheets containing Lorem Ipsum passages, and more recently with desktop publishing software.</p>
  <span class="btn btn-orange" style="left:78px;top:2680px;width:168px;height:60px">Read More</span>
  <div class="ph" role="img" aria-label="Photo of a grey residential room with a red sofa and framed pictures" style="left:598px;top:2321px;width:602px;height:474px;background:radial-gradient(ellipse 22% 9% at 78% 66%,#c2304a,transparent 75%),radial-gradient(ellipse 25% 8% at 40% 33%,#f4f4f4,transparent 75%),linear-gradient(180deg,#7e7e7e,#a9a9a9 62%,#e6e6e6 70%,#f2f2f2)"></div>
</section>

<section class="products">
  <h2>Our Products</h2>
  <div class="arrow" style="left:1026px;top:30px;width:40px;height:40px;background:var(--orange)"><svg width="12" height="16"><polyline points="9,2 3,8 9,14" fill="none" stroke="#fff" stroke-width="2.5"/></svg></div>
  <div class="arrow" style="left:1074px;top:30px;width:40px;height:40px;background:var(--blue)"><svg width="12" height="16"><polyline points="3,2 9,8 3,14" fill="none" stroke="#fff" stroke-width="2.5"/></svg></div>
  <div class="card" style="left:78px">
    <div class="ph" role="img" aria-label="Product photo of an ornate bronze and silver side table" style="background-image:radial-gradient(ellipse 32% 38% at 50% 45%,#7a6a55,#a89b86 45%,rgba(255,255,255,0) 100%)"></div>
    <div class="card-actions">
      <span><svg width="14" height="13"><path d="M7 12 L1 6 A3 3 0 0 1 7 3 A3 3 0 0 1 13 6 Z" fill="none" stroke="#fff" stroke-width="1.5"/></svg></span>
      <span><svg width="16" height="10"><ellipse cx="8" cy="5" rx="7" ry="4" fill="none" stroke="#fff" stroke-width="1.5"/><circle cx="8" cy="5" r="1.8" fill="#fff"/></svg></span>
      <span><svg width="14" height="14"><path d="M1 2h2l2 8h7l1-6H4" fill="none" stroke="#fff" stroke-width="1.5"/></svg></span>
    </div>
    <h5>Product Shop</h5><div class="stars">★★★★☆</div><div class="old">$ 500</div><div class="price">$ 450</div>
  </div>
  <div class="card" style="left:340px">
    <div class="ph" role="img" aria-label="Product photo of a black and gold dining chair" style="background-image:radial-gradient(ellipse 22% 40% at 50% 50%,#2a2620,#8a7440 55%,rgba(255,255,255,0) 100%)"></div>
    <h5>Product Shop</h5><div class="stars">★★★★☆</div><div class="old">$ 500</div><div class="price">$ 450</div>
  </div>
  <div class="card" style="left:602px">
    <div class="ph" role="img" aria-label="Product photo of a grey upholstered armchair with wooden legs" style="background-image:radial-gradient(ellipse 34% 32% at 50% 50%,#9c9c9a,#c4c2bd 50%,rgba(255,255,255,0) 100%)"></div>
    <h5>Product Shop</h5><div class="stars">★★★★☆</div><div class="old">$ 500</div><div class="price">$ 450</div>
  </div>
  <div class="card" style="left:864px">
    <div class="ph" role="img" aria-label="Product photo of a pair of upholstered stools" style="background-image:radial-gradient(ellipse 38% 22% at 50% 50%,#8d8a84,#bdb9b1 50%,rgba(255,255,255,0) 100%)"></div>
    <h5>Product Shop</h5><div class="stars">★★★★☆</div><div class="old">$ 500</div><div class="price">$ 450</div>
  </div>
</section>

<section>
  <h2 class="rule-title" style="top:3440px;color:var(--blue)"><i></i>Our Catalog<i></i></h2>
  <div class="tile ph" role="img" aria-label="Catalog photo of a bright bedroom with wooden floor" style="left:0;top:3535px;background:linear-gradient(180deg,#e9e6e1 0%,#d8d3cb 60%,#a57c55 62%,#8c6644 100%)"></div>
  <div class="tile ph" role="img" aria-label="Catalog photo of a white room with window and desk" style="left:303px;top:3535px;background:linear-gradient(90deg,#f2f1ee 0%,#f2f1ee 40%,#d8dde2 41%,#d8dde2 60%,#e7e5e1 61%),linear-gradient(180deg,#eee,#b6ada0)"></div>
  <div class="tile ph" role="img" aria-label="Catalog photo of a living corner with chair and round clock" style="left:606px;top:3535px;background:radial-gradient(circle at 55% 28%,#3a3a3a 0 7%,transparent 8%),radial-gradient(ellipse 20% 22% at 30% 72%,#7b6650,transparent 75%),linear-gradient(180deg,#f0efec,#d9d3ca)"></div>
  <div class="tile ph" role="img" aria-label="Catalog photo of a minimal white interior" style="left:910px;top:3535px;background:linear-gradient(180deg,#f5f5f5 0%,#e2e2e2 65%,#bdbdbd 100%)"></div>
  <div class="tile ph" role="img" aria-label="Catalog photo of a colourful shelving wall" style="left:0;top:3757px;background:linear-gradient(90deg,#e4d3b4 0 22%,#f3a53b 22% 34%,#2f5f96 34% 52%,#d9c7a3 52% 70%,#e8e6e2 70%)"></div>
  <div class="tile ph" role="img" aria-label="Catalog photo of a white kitchen with wooden stools" style="left:303px;top:3757px;background:radial-gradient(ellipse 30% 14% at 50% 78%,#b08a62,transparent 75%),linear-gradient(180deg,#f4f3f1,#dcd7cf)"></div>
  <div class="tile ph" role="img" aria-label="Catalog photo of a bathroom with freestanding tub" style="left:606px;top:3757px;background:radial-gradient(ellipse 28% 16% at 50% 70%,#ffffff,transparent 75%),linear-gradient(180deg,#d6d1c8,#ebe8e3 60%,#9b9186)"></div>
  <div class="tile ph" role="img" aria-label="Catalog photo of a dark sideboard in a white room" style="left:910px;top:3757px;background:linear-gradient(180deg,#f0f0f0 0%,#f0f0f0 45%,#2e2e2e 46%,#3a3a3a 68%,#e4e4e4 69%)"></div>
  <span class="btn btn-orange" style="left:512px;top:4020px;width:176px;height:60px">View All</span>
</section>

<section class="newsletter">
  <div class="ph" role="img" aria-label="Photo of a white sofa with vase and side table" style="inset:0;background:radial-gradient(ellipse 12% 40% at 8% 60%,#b9b6b0,transparent 75%),radial-gradient(ellipse 10% 20% at 88% 80%,#a59c90,transparent 75%),linear-gradient(90deg,#dedbd5,#f3f2ef 50%,#d2cdc4)"></div>
  <h2>Interior Design Newsletter</h2>
  <p>Sign Up for Our Newsletter to get Latest Updates and Offers. Subscribe to receive news in your inbox.</p>
  <div class="field">Enter Email Address :</div>
  <span class="btn btn-blue" style="left:750px;top:268px;width:168px;height:62px">Subscribe</span>
</section>

<section class="articles">
  <h2 class="rule-title" style="top:50px;color:#fff"><i></i>LORI VEX ARTICALS<i></i></h2>
  <div class="mag" style="left:107px"><div class="ph" role="img" aria-label="Magazine article spread on interior design" style="inset:14px;background:linear-gradient(135deg,#f3efe9,#c7b9a6)"></div></div>
  <div class="mag" style="left:374px"><div class="ph" role="img" aria-label="Lumen magazine cover in black and white" style="inset:14px;background:linear-gradient(180deg,#e7e7e7,#6b6b6b)"></div></div>
  <div class="mag" style="left:641px"><div class="ph" role="img" aria-label="Lumen magazine cover with blue and purple tones" style="inset:14px;background:linear-gradient(180deg,#5b6fc6,#8c4a9a)"></div></div>
  <div class="mag" style="left:908px"><div class="ph" role="img" aria-label="Magazine article spread with interior photos" style="inset:14px;background:linear-gradient(135deg,#f4f1ec,#b98f68)"></div></div>
</section>

<footer class="footer">
  <h4 style="left:78px;top:60px">ADDRESS</h4>
  <div class="lines" style="left:78px;top:100px"><span class="hl">LORI VEX STUDIO</span><br>Lori Vex Design House<br>18 Fenwick Ave, Marlow, CA 90210</div>
  <div class="brand-mark" style="top:40px"><div class="sq" style="width:48px;height:48px;border-color:#8a7560"></div><span style="color:#8a7560;font-size:13px">LORI VEX STUDIO</span></div>
  <h4 style="left:872px;top:60px">CONTACT US</h4>
  <div class="lines" style="left:872px;top:100px"><span class="hl">Tel:</span> 555-014-2207<br><span class="hl">Email:</span> info@lorivexstudio.com</div>
  <div class="foot-nav">About | Services | Shop | Portfolio | Blog | Contact</div>
</footer>
<div class="copy">© 2018 Lori Vex Design House | Design and Development: Fernloft, LLC | Powered by Quillbase</div>

</body>
</html>
```